Stationery Design Project for High End Wealth Management Firm

We need a stationery design for our high-end wealth management firm. Our clientele are affluent and our brand is built around providing investment services with world-class service.

The final concepts should provide a business card, letterhead, and envelope.

We like the idea of having text on the front and back and we MUST have black front and back business cards.
For the business card we have the following that needs to be included:
Company Logo & Tagline
Employee Name
Employee title
Employee Email
Website
2 seperate office cities, addresses, and phone numbers
Financial disclosure (small print)

Having black envelopes would be neat, but black is not a must for the envelopes.
Updates

Project Deadline Extended
Reason: To give the concept one more day of revisions.

Project Deadline Extended
Reason: To allow for more concepts and designs.

Target Market(s)

High Net Worth

Industry/Entity Type

Business

Requirements
Must have
• The following disclosure must be on the back of the card in small print:

Investment Advisory Services offered through Harrowfield Asset Partners LLC, a NFR Registered Investment Advisor. Vantory Wealth Management LLC is not affiliated with Harrowfield Asset Partners LLC.

Black business cards are also a must have.

Please utilize each of the 3 components of our logo in the design.

Please use our white background logo elements when designing our letterhead if you need them.
Nice to have
• Please use our company colors when designing. Utilize a combination of the elements of our logo that we have attached.

We are going to be printing our business cards on letterpress.

```html
<!DOCTYPE html>
<html lang="en">
<head>
<meta charset="utf-8">
<title>Vantory Wealth Management – Business Card</title>
<link href="https://fonts.googleapis.com/css2?family=Jost:wght@400;500&family=Arimo:wght@400&display=swap" rel="stylesheet">
<style>
  :root {
    --backdrop: #c8d2d5;
    --card: #2a2a2a;
    --text: #d9d9d9;
    --muted: #bdbdbd;
    --gold: #c9a35c;
  }
  * { margin: 0; padding: 0; box-sizing: border-box; }
  html, body { width: 1200px; height: 960px; overflow: hidden; }
  body {
    background: var(--backdrop);
    font-family: "Jost", sans-serif;
    color: var(--text);
    position: relative;
  }
  .card {
    position: absolute;
    left: 300px;
    width: 600px;
    height: 343px;
    background: var(--card);
    border-radius: 3px;
    box-shadow: 0 6px 18px rgba(0,0,0,0.25);
    overflow: hidden;
  }
  .card--back { top: 100px; }
  .card--front { top: 517px; }

  .brand {
    display: flex;
    align-items: center;
    gap: 12px;
    font-weight: 400;
    color: var(--text);
    letter-spacing: 0.06em;
    text-transform: uppercase;
    white-space: nowrap;
  }
  .brand__mark {
    border-radius: 50%;
    background: var(--gold);
    flex: none;
  }

  .card--back .brand {
    position: absolute;
    top: 34px;
    right: 26px;
    font-size: 17px;
  }
  .card--back .brand__mark { width: 14px; height: 14px; }

  .person { position: absolute; left: 30px; top: 86px; }
  .person__name, .person__title { font-size: 22px; font-weight: 400; line-height: 1.35; }

  .contact { position: absolute; left: 30px; top: 158px; font-size: 14px; line-height: 1.5; }
  .contact__row { display: flex; align-items: center; gap: 8px; }
  .contact__row svg { width: 11px; height: 11px; flex: none; }

  .office { position: absolute; font-style: normal; line-height: 1.35; }
  .office--primary { left: 30px; top: 212px; font-size: 16px; }
  .office--secondary { left: 336px; top: 190px; font-size: 14px; }
  .office__phone { display: flex; align-items: center; gap: 8px; }
  .office__phone svg { width: 10px; height: 12px; flex: none; }

  .disclosure {
    position: absolute;
    left: 30px;
    right: 26px;
    bottom: 14px;
    font-size: 10px;
    line-height: 1.35;
    color: var(--muted);
  }

  .card--front .brand {
    position: absolute;
    top: 100px;
    left: 0;
    right: 0;
    justify-content: center;
    font-size: 26px;
    gap: 16px;
  }
  .card--front .brand__mark { width: 40px; height: 40px; }
  .tagline {
    position: absolute;
    left: 0;
    right: 0;
    top: 218px;
    text-align: center;
    font-family: "Arimo", sans-serif;
    font-size: 16px;
    color: var(--text);
  }
</style>
</head>
<body>
  <section class="card card--back" aria-label="Business card, contact side">
    <div class="brand"><span class="brand__mark"></span>Vantory Wealth Management</div>

    <div class="person">
      <p class="person__name">Dana Whitlow</p>
      <p class="person__title">Director</p>
    </div>

    <div class="contact">
      <p class="contact__row">
        <svg viewBox="0 0 12 10"><rect x="0.5" y="0.5" width="11" height="9" fill="none" stroke="#d9d9d9"/><path d="M0.5 0.5 L6 5.5 L11.5 0.5" fill="none" stroke="#d9d9d9"/></svg>
        dwhitlow@mailbox.com
      </p>
      <p class="contact__row">
        <svg viewBox="0 0 12 12"><circle cx="6" cy="6" r="5.3" fill="none" stroke="#d9d9d9"/><ellipse cx="6" cy="6" rx="2.3" ry="5.3" fill="none" stroke="#d9d9d9"/><path d="M0.7 6 H11.3" stroke="#d9d9d9"/></svg>
        www.vantorywealth.com
      </p>
    </div>

    <address class="office office--primary">
      <p>Elm Ridge 14 Carrow Street</p>
      <p>Elm Ridge SA 5102</p>
      <p class="office__phone">
        <svg viewBox="0 0 10 12"><path d="M3 1 L1.5 2.5 C1 6 4 10.5 7.5 11 L9 9.5 L7 7.8 L6 8.6 C4.5 7.8 3.4 6 3.2 4.6 L4.3 4 Z" fill="#d9d9d9"/></svg>
        8314 6620
      </p>
    </address>

    <address class="office office--secondary">
      <p>Elm Ridge 14 Carrow Street</p>
      <p>Elm Ridge SA 5102</p>
      <p class="office__phone">
        <svg viewBox="0 0 10 12"><path d="M3 1 L1.5 2.5 C1 6 4 10.5 7.5 11 L9 9.5 L7 7.8 L6 8.6 C4.5 7.8 3.4 6 3.2 4.6 L4.3 4 Z" fill="#d9d9d9"/></svg>
        8314 6620
      </p>
    </address>

    <p class="disclosure">Investment Advisory Services offered through Harrowfield Asset Partners LLC, a NFR Registered Investment Advisor. Vantory Wealth Management LLC is not affiliated with Harrowfield Asset Partners LLC.</p>
  </section>

  <section class="card card--front" aria-label="Business card, brand side">
    <div class="brand"><span class="brand__mark"></span>Vantory Wealth Management</div>
    <p class="tagline">Preferred Wealth Management for Select Individuals</p>
  </section>
</body>
</html>
```